Website for "Bright Morrow Ltd" cleaning bsuiness

We require a website to expose our business to the local market. We want to provide background on who we are and what we do but in an easily digestible way. We clean domestic and commercial premises and want to provide a list of all of our services to potential customers. We operate out of Warrington in the UK.

We would like the website to be animated in some way so that the experience of using it is not dull or mundane. This website needs to be an extension of our company.

Target Market(s)

30 - 60 year olds for Domestic plus commercial clients

Industry/Entity Type

Cleaning Service

Coding

Coded - Design and coding required

Number of Pages Required

4 page

Font styles to use
Sans Serif

Colors
0455a3
3176b5
85acd3
cfdeed
ffffff
000000
1b1b1b
c8c8c8
757575

Requirements
Must have
• Logo which has been provided. Theme based around the logo and its colours. Simple layout to avoid confusion.
Nice to have
• Animations where possible to impress the customer.
Should not have
• any pictures of cleaning equipment, fairies, maids etc

```html
<!DOCTYPE html>
<html lang="en">
<head>
<meta charset="utf-8">
<title>Bright Morrow Ltd — Professional Cleaning Service</title>
<link href="https://fonts.googleapis.com/css2?family=Lato:wght@400;700;900&family=Raleway:wght@300;400;500&display=swap" rel="stylesheet">
<style>
:root{
  --navy:#1a2c92;
  --royal:#1d3bb8;
  --bright:#1c47d9;
  --deep:#16278a;
  --band-a:#1a2f96;
  --band-b:#1737b2;
  --band-c:#1845d6;
  --ink:#1b1b1b;
  --body:#555555;
  --muted:#757575;
  --line:#c8c8c8;
  --pale:#cfdeed;
  --white:#ffffff;
  --footer:#f3f4f6;
}
*{box-sizing:border-box;margin:0;padding:0}
html,body{width:1200px;height:3734px;overflow:hidden}
body{font-family:"Lato",sans-serif;color:var(--body);background:var(--white);position:relative}
section,header,footer{position:absolute;left:0;width:1200px}
a{color:inherit;text-decoration:none}

/* header */
.site-header{top:0;height:130px;background:var(--white);border-bottom:3px solid var(--navy)}
.brand{position:absolute;left:80px;top:34px;display:flex;align-items:center;gap:12px}
.brand-dot{width:34px;height:34px;border-radius:50%;background:var(--navy)}
.brand-name{font-family:"Lato",sans-serif;font-weight:700;font-size:26px;color:var(--navy);line-height:1.1;width:150px}
.social-top{position:absolute;top:20px;right:88px;display:flex;gap:22px}
.social-top span{width:24px;height:24px;border-radius:50%;background:#c2c6d2}
.social-top span:first-child{background:var(--navy)}
.main-nav{position:absolute;left:344px;top:82px;display:flex}
.main-nav a{font-family:"Lato",sans-serif;font-size:17px;color:var(--royal);letter-spacing:.5px;position:absolute;white-space:nowrap}
.main-nav a.active{color:var(--ink)}
.main-nav a.active::after{content:"";position:absolute;left:-20px;right:-20px;top:38px;height:6px;background:var(--navy)}

/* hero */
.hero{top:130px;height:672px}
.hero-photo{position:absolute;inset:0;background:linear-gradient(100deg,#eef0ef 0%,#e3e5e2 40%,#d9dcda 65%,#c9ccca 100%)}
.hero-copy{position:absolute;left:78px;top:170px}
.hero-title{font-family:"Lato",sans-serif;font-weight:900;font-size:76px;color:var(--navy);letter-spacing:1px;line-height:1}
.hero-sub{font-family:"Lato",sans-serif;font-size:40px;color:#2a2a2a;line-height:45px;margin-top:20px;text-transform:uppercase}
.btn-quote{position:absolute;left:0;top:358px;width:155px;height:45px;background:var(--navy);color:var(--white);font-size:17px;display:flex;align-items:center;justify-content:center;border-radius:3px;letter-spacing:.5px}

/* info band */
.info-band{top:789px;left:77px;width:1046px;height:227px;display:flex}
.info-item{flex:1;display:flex;flex-direction:column;align-items:center;color:var(--white);padding-top:34px}
.info-item:nth-child(1){background:var(--band-a)}
.info-item:nth-child(2){background:var(--band-b)}
.info-item:nth-child(3){background:var(--band-c)}
.info-item svg{width:50px;height:50px}
.info-label{font-size:22px;margin-top:30px}
.info-value{font-size:19px;margin-top:18px}
.info-item:nth-child(2) .info-value{font-size:28px;margin-top:14px;letter-spacing:1px}

/* welcome */
.welcome{top:1016px;height:632px;text-align:center}
.kicker{font-family:"Raleway",sans-serif;font-size:17px;letter-spacing:1.5px;color:var(--ink);text-transform:uppercase}
.section-title{font-family:"Raleway",sans-serif;font-weight:400;font-size:42px;color:var(--navy)}
.welcome .kicker{margin-top:44px}
.welcome .section-title{margin-top:2px}
.welcome-intro{width:930px;margin:20px auto 0;font-size:14px;line-height:25px;color:var(--body)}
.feature-row{position:absolute;top:239px;left:0;width:1200px}
.feature{position:absolute;width:300px;text-align:center}
.feature-photo{width:220px;height:220px;border-radius:50%;margin:0 auto;border:3px solid var(--navy);padding:4px;background-clip:content-box}
.feature h3{font-family:"Lato",sans-serif;font-weight:400;font-size:20px;color:var(--ink);margin-top:26px}
.feature p{font-size:14px;line-height:25px;margin-top:10px;color:var(--body)}
.feature .more{display:block;font-size:15px;color:var(--navy);margin-top:6px;letter-spacing:.5px}
.slider-arrow{position:absolute;top:333px;width:24px;height:50px}

/* services */
.services{top:1648px;height:700px;background:linear-gradient(120deg,#2a47c9 0%,#3253d4 45%,#3a5fe0 100%);text-align:center}
.services .kicker{color:var(--white);margin-top:42px}
.services .section-title{color:var(--white);font-weight:300;margin-top:0}
.card{position:absolute;width:233px;height:230px;background:var(--white);text-align:left}
.card-photo{height:152px;margin:0;position:relative}
.card-label{font-size:16px;line-height:22px;color:var(--bright);padding:12px 12px 0}
.card-featured .card-label{color:var(--ink);text-align:center;font-size:16px;padding-top:10px}
.read-more{position:absolute;left:47px;top:62px;width:140px;height:38px;background:#4f7de8;color:var(--white);font-size:15px;display:flex;align-items:center;justify-content:center;letter-spacing:.5px}

/* testimonial */
.testimonial{top:2348px;height:498px;text-align:center}
.testimonial .kicker{margin-top:52px}
.testimonial .section-title{margin-top:0;font-size:44px}
.quote-mark{position:absolute;left:180px;top:126px;font-family:"Raleway",sans-serif;font-size:60px;color:var(--line)}
.quote-box{position:absolute;left:232px;top:154px;width:727px;height:195px;border:2px solid #d6d6d6;padding:38px 60px;font-size:15px;line-height:27px;color:var(--body)}
.quote-tail{position:absolute;left:856px;top:347px}
.client{position:absolute;right:386px;top:397px;text-align:right;font-size:14px;line-height:25px;color:var(--ink)}
.client-photo{position:absolute;left:839px;top:374px;width:84px;height:84px;border-radius:50%;background:linear-gradient(160deg,#6b5a50,#c9b7a8);border:3px solid var(--white);box-shadow:0 0 0 1px var(--line)}

/* booking */
.booking{top:2846px;height:523px;background:linear-gradient(110deg,#c7daf3 0%,#e3edf9 45%,#d3e2f5 100%)}
.booking-photo{position:absolute;left:0;top:40px;width:500px;height:483px;background:linear-gradient(180deg,#d8e5f4 0%,#9fb9da 50%,#3e7fc9 100%)}
.booking-card{position:absolute;left:550px;top:50px;width:521px;height:473px;background:var(--white);padding:0 60px}
.booking-card h2{font-family:"Raleway",sans-serif;font-weight:400;font-size:38px;color:var(--navy);margin-top:30px;letter-spacing:.5px}
.field{position:absolute;border:1px solid var(--line);font-size:12px;color:var(--muted);padding:0 12px;display:flex;align-items:center}
.field.textarea{align-items:flex-start;padding-top:12px}
.field svg{position:absolute;right:14px;top:18px}
.btn-submit{position:absolute;left:50px;top:388px;width:172px;height:45px;background:var(--bright);color:var(--white);font-size:18px;display:flex;align-items:center;justify-content:center;letter-spacing:.5px}

/* footer */
.site-footer{top:3369px;height:316px;background:var(--footer)}
.footer-brand{position:absolute;left:82px;top:70px;display:flex;align-items:center;gap:12px}
.footer-about{position:absolute;left:82px;top:206px;width:220px;font-size:14px;line-height:26px;color:var(--ink)}
.footer-col{position:absolute;top:60px}
.footer-col h4{font-family:"Lato",sans-serif;font-weight:400;font-size:19px;color:var(--navy);margin-bottom:14px}
.footer-col li{list-style:none;font-size:13px;line-height:25px;color:var(--muted)}
.footer-col li::before{content:"› ";color:var(--muted)}
.contact-line{display:flex;gap:12px;font-size:14px;line-height:22px;color:var(--muted);margin-bottom:20px}
.contact-line svg{flex:none;margin-top:3px}
.social-foot{position:absolute;left:964px;top:245px;display:flex;gap:6px}
.social-foot span{width:48px;height:48px;border-radius:50%;border:2px solid var(--bright);background:var(--white)}
.social-foot span:first-child{background:var(--bright)}
.copyright{position:absolute;left:0;top:3685px;width:1200px;height:49px;background:var(--deep);color:var(--white);font-size:14px;display:flex;align-items:center;justify-content:center}
.copyright strong{color:#8fb1f5;font-weight:700;margin-right:4px}
</style>
</head>
<body>

<header class="site-header">
  <div class="brand"><span class="brand-dot"></span><span class="brand-name">Bright Morrow Ltd</span></div>
  <div class="social-top"><span></span><span></span><span></span></div>
  <nav class="main-nav">
    <a class="active" href="#" style="left:0">HOME</a>
    <a href="#" style="left:128px">ABOUT</a>
    <a href="#" style="left:262px">SERVICES</a>
    <a href="#" style="left:414px">GALLERY</a>
    <a href="#" style="left:542px">BLOGS</a>
    <a href="#" style="left:700px">CONTACT</a>
  </nav>
</header>

<section class="hero">
  <div class="hero-photo" role="img" aria-label="Bright living room with a sofa and plants, someone vacuuming the floor"></div>
  <div class="hero-copy">
    <h1 class="hero-title">CLEAN HOME</h1>
    <p class="hero-sub">Professional service,<br>fair price.</p>
    <a class="btn-quote" href="#">QUICK QUOTE</a>
  </div>
</section>

<section class="info-band">
  <div class="info-item">
    <svg viewBox="0 0 50 50" fill="none" stroke="#fff" stroke-width="3"><rect x="5" y="9" width="40" height="36" rx="3"/><line x1="5" y1="19" x2="45" y2="19"/><line x1="15" y1="4" x2="15" y2="13"/><line x1="35" y1="4" x2="35" y2="13"/><g fill="#fff" stroke="none"><rect x="11" y="24" width="6" height="5"/><rect x="22" y="24" width="6" height="5"/><rect x="33" y="24" width="6" height="5"/><rect x="11" y="33" width="6" height="5"/><rect x="22" y="33" width="6" height="5"/><rect x="33" y="33" width="6" height="5"/></g></svg>
    <div class="info-label">We Are Open</div>
    <div class="info-value">Mon - Fri : 9:00 a.m To 8:00 p.m</div>
  </div>
  <div class="info-item">
    <svg viewBox="0 0 50 50" fill="none" stroke="#fff" stroke-width="3"><rect x="14" y="3" width="22" height="44" rx="4"/><line x1="14" y1="38" x2="36" y2="38"/><line x1="21" y1="8" x2="29" y2="8"/><circle cx="25" cy="42.5" r="1.5" fill="#fff"/></svg>
    <div class="info-label">Call Us Now</div>
    <div class="info-value">123 456 7878</div>
  </div>
  <div class="info-item">
    <svg viewBox="0 0 50 50" fill="none" stroke="#fff" stroke-width="3"><rect x="4" y="10" width="42" height="30" rx="2"/><polyline points="4,11 25,28 46,11"/></svg>
    <div class="info-label">Order The Services By mail</div>
    <div class="info-value">hello@brightmorrow.co.uk</div>
  </div>
</section>

<section class="welcome">
  <p class="kicker">Welcome to our site</p>
  <h2 class="section-title">Professional Cleaning Service Company</h2>
  <p class="welcome-intro">Lorem Ipsum is simply dummy text of the printing and typesetting industry. Lorem Ipsum has been the industry's standard dummy text ever since the 1500s, when an unknown printer took a galley of type and scrambled it to make a type specimen book.It has survived not only five centuries, but also the leap into electronic typesetting, remaining essentially unchanged.</p>
  <svg class="slider-arrow" style="left:28px" viewBox="0 0 24 50" fill="none" stroke="#b5b5b5" stroke-width="2"><polyline points="20,4 4,25 20,46"/></svg>
  <svg class="slider-arrow" style="left:1150px" viewBox="0 0 24 50" fill="none" stroke="#b5b5b5" stroke-width="2"><polyline points="4,4 20,25 4,46"/></svg>
  <div class="feature-row">
    <div class="feature" style="left:84px">
      <div class="feature-photo" role="img" aria-label="Contract daily cleaning photo" style="background-color:#c9d9ea;background-image:linear-gradient(160deg,#e6eef5,#8fb0d6)"></div>
      <h3>Contract daily cleaning</h3>
      <p>Lorem Ipsum is simply dummy text of the<br>printing and typesetting industry.</p>
      <a class="more" href="#">READMORE »</a>
    </div>
    <div class="feature" style="left:450px">
      <div class="feature-photo" role="img" aria-label="Vacuuming a carpet photo" style="background-image:linear-gradient(160deg,#f0f0f0,#9a9a9a)"></div>
      <h3>Vacuuming</h3>
      <p>Lorem Ipsum is simply dummy text of the<br>printing and typesetting industry.</p>
      <a class="more" href="#">READMORE »</a>
    </div>
    <div class="feature" style="left:816px">
      <div class="feature-photo" role="img" aria-label="Desk polishing photo" style="background-image:linear-gradient(160deg,#9aa3ad,#5a3f2e)"></div>
      <h3>Desk polishing</h3>
      <p>Lorem Ipsum is simply dummy text of the<br>printing and typesetting industry.</p>
      <a class="more" href="#">READMORE »</a>
    </div>
  </div>
</section>

<section class="services">
  <p class="kicker">We make life easier</p>
  <h2 class="section-title">OUR SERVICES</h2>

  <div class="card card-featured" style="left:77px;top:132px">
    <div class="card-photo" role="img" aria-label="Wiping a surface photo" style="background:linear-gradient(160deg,#fbfbfb,#d9dde4)"><span class="read-more">READ MORE</span></div>
    <p class="card-label">Weekly, fotnightly, monthly<br>and adhoc cleans available</p>
  </div>
  <div class="card" style="left:349px;top:132px">
    <div class="card-photo" role="img" aria-label="Carpet cleaning photo" style="background:linear-gradient(160deg,#e9e4dd,#9c8f80)"></div>
    <p class="card-label">Carpet Cleaning</p>
  </div>
  <div class="card" style="left:620px;top:132px">
    <div class="card-photo" role="img" aria-label="Ironing photo" style="background:linear-gradient(160deg,#7b5a86,#c9bfd2)"></div>
    <p class="card-label">Ironing</p>
  </div>
  <div class="card" style="left:891px;top:132px">
    <div class="card-photo" role="img" aria-label="Tiled floor steam clean photo" style="background:linear-gradient(160deg,#9aa4a8,#5d676b)"></div>
    <p class="card-label">Tiled floor steam clean</p>
  </div>
  <div class="card" style="left:77px;top:409px">
    <div class="card-photo" role="img" aria-label="Empty kitchen after end of tenancy clean photo" style="background:linear-gradient(160deg,#6a6450,#2b2a26)"></div>
    <p class="card-label">End of tenancy clean</p>
  </div>
  <div class="card" style="left:349px;top:409px">
    <div class="card-photo" role="img" aria-label="Cleaning team in a new house photo" style="background:linear-gradient(160deg,#9c6a3c,#3c5a8c)"></div>
    <p class="card-label">New house pre moving<br>in clean</p>
  </div>
  <div class="card" style="left:620px;top:409px">
    <div class="card-photo" role="img" aria-label="Emergency bathroom clean photo" style="background:linear-gradient(160deg,#8d8a86,#3c3b3a)"></div>
    <p class="card-label">Emergency requested<br>clean</p>
  </div>
  <div class="card" style="left:891px;top:409px">
    <div class="card-photo" role="img" aria-label="Commercial office clean photo" style="background:linear-gradient(160deg,#c4a789,#d8d8d2)"></div>
    <p class="card-label">Commercial clean</p>
  </div>
</section>

<section class="testimonial">
  <p class="kicker">What our customer say</p>
  <h2 class="section-title">TESTIMONIAL</h2>
  <span class="quote-mark">“</span>
  <blockquote class="quote-box">Lorem Ipsum is simply dummy text of the printing and typesetting industry. Lorem Ipsum has been the industry's standard dummy text ever since the 1500s, when an unknown printer took a galley of type and scrambled it to make a type specimen book.It has survived not only five centuries, but also the leap into electronic typesetting, remaining essentially unchanged.</blockquote>
  <svg class="quote-tail" width="40" height="22" viewBox="0 0 40 22"><polygon points="0,0 40,0 20,20" fill="#fff"/><polyline points="0,1 20,20 40,1" fill="none" stroke="#d6d6d6" stroke-width="2"/></svg>
  <div class="client">Customer Name<br>Client</div>
  <div class="client-photo" role="img" aria-label="Client portrait"></div>
</section>

<section class="booking">
  <div class="booking-photo" role="img" aria-label="Smiling cleaner holding a bucket of cleaning supplies"></div>
  <form class="booking-card">
    <h2>BOOK SERVICE</h2>
    <div class="field" style="left:50px;top:87px;width:202px;height:45px">Name</div>
    <div class="field" style="left:259px;top:87px;width:202px;height:45px">Contact No</div>
    <div class="field" style="left:50px;top:139px;width:202px;height:48px">Choose Service
      <svg width="18" height="10" viewBox="0 0 18 10" fill="none" stroke="#999" stroke-width="2"><polyline points="1,1 9,8 17,1"/></svg></div>
    <div class="field" style="left:259px;top:139px;width:202px;height:48px">Date</div>
    <div class="field" style="left:50px;top:192px;width:411px;height:44px">Email Id</div>
    <div class="field textarea" style="left:50px;top:241px;width:411px;height:88px">Message...</div>
    <span class="btn-submit">SUBMIT</span>
  </form>
</section>

<footer class="site-footer">
  <div class="footer-brand"><span class="brand-dot"></span><span class="brand-name">Bright Morrow Ltd</span></div>
  <p class="footer-about">Lorem Ipsum is simply dummy text of the printing and typesetting industry.</p>
  <div class="footer-col" style="left:349px">
    <h4>Navigation</h4>
    <ul><li>Home</li><li>About</li><li>Service</li><li>Gallery</li><li>Blogs</li><li>Contact</li></ul>
  </div>
  <div class="footer-col" style="left:618px">
    <h4>Services</h4>
    <ul><li>Weekly, monthly and adhoc cleans</li><li>Carpet Cleaning</li><li>Ironing</li><li>Tiled floor steam clean</li><li>End of tenancy clean</li><li>New house pre moving in clean</li><li>Emergency requested clean</li></ul>
  </div>
  <div class="footer-col" style="left:891px">
    <h4>Contact Information</h4>
    <div class="contact-line"><svg width="14" height="18" viewBox="0 0 14 18"><path d="M7 0C3 0 0 3 0 7c0 5 7 11 7 11s7-6 7-11c0-4-3-7-7-7zm0 10a3 3 0 110-6 3 3 0 010 6z" fill="#8a8a8a"/></svg><span>123,Lorem Ipsum,Street<br>Country,Zip Code.</span></div>
    <div class="contact-line"><svg width="16" height="16" viewBox="0 0 16 16"><path d="M3 1l3 3-2 2c1 2 3 4 5 5l2-2 3 3-2 3C6 15 1 10 0 3z" fill="#8a8a8a"/></svg><span>123 456 7878</span></div>
    <div class="contact-line"><svg width="16" height="12" viewBox="0 0 16 12" fill="none" stroke="#8a8a8a" stroke-width="1.5"><rect x="1" y="1" width="14" height="10"/><polyline points="1,1 8,7 15,1"/></svg><span>hello@brightmorrow.co.uk</span></div>
  </div>
  <div class="social-foot"><span></span><span></span><span></span></div>
</footer>
<div class="copyright"><strong>© Bright Morrow Ltd</strong> - 2016 All Right Reserved</div>

</body>
</html>
```